VELMOR Website Design

We need a website designed for our company VELMOR. We are a luxury lifestyle club that will provide benefits and services for our members. The site should be clean & sleek, preferably using black and white (or darker colors). (example sites: stravenhall.example, plinth.example)

Here is a link of a sample page I did using wix. (https://dunmere7.sitehostly.example/mysite) This can be used to get a general idea.

Target Market(s)

Upper Middle Class in the United States

Number of Pages Required

5+ page

Font styles to use
Sans Serif
Other font styles liked:
• Arial (or other similar fonts)

Requirements
Must have
• A clean design that is eye-catching and speaks to our company.
Nice to have
• Ideas for copy.

```html
<!DOCTYPE html>
<html lang="en">
<head>
<meta charset="UTF-8">
<title>VELMOR — About &amp; Services</title>
<link href="https://fonts.googleapis.com/css2?family=Montserrat:wght@700&family=Roboto:wght@400;500&display=swap" rel="stylesheet">
<style>
  :root {
    --ink: #3d3d3d;
    --body-text: #5f6266;
    --accent: #1ec0ee;
    --frame: #d5dada;
    --dark: #3e4145;
    --dark-deep: #34373b;
    --white: #ffffff;
  }
  * { box-sizing: border-box; margin: 0; padding: 0; }
  html, body { width: 1200px; height: 1032px; overflow: hidden; background: var(--white); }
  body { position: relative; font-family: "Roboto", Arial, sans-serif; }

  .about { position: absolute; left: 0; top: 0; width: 1200px; height: 366px; background: var(--white); }
  .about__title {
    position: absolute; left: 132px; top: 52px;
    font-family: "Montserrat", Arial, sans-serif; font-weight: 700;
    font-size: 32px; color: var(--ink); letter-spacing: 0.2px;
  }
  .about__text {
    position: absolute; left: 131px; width: 430px;
    font-size: 12.6px; line-height: 21px; color: var(--body-text); letter-spacing: 0.3px;
  }
  .about__text--first { top: 110px; }
  .about__text--second { top: 193px; }

  .button {
    position: absolute; width: 126px; height: 38px;
    background: var(--accent); color: var(--white);
    font-family: "Roboto", Arial, sans-serif; font-weight: 500; font-size: 12.5px;
    display: flex; align-items: center; justify-content: center;
    text-decoration: none; letter-spacing: 0.2px;
  }
  .button--learn { left: 132px; top: 256px; }
  .button--apply { left: 537px; top: 938px; }

  .services {
    position: absolute; left: 0; top: 366px; width: 1200px; height: 666px;
    background: radial-gradient(ellipse at 30% 40%, #4a4d52 0%, var(--dark) 45%, var(--dark-deep) 100%);
  }

  .about__frame {
    position: absolute; left: 602px; top: 38px; width: 438px; height: 314px;
    border: 5px solid var(--frame); z-index: 2;
  }
  .about__photo {
    position: absolute; left: 650px; top: 86px; width: 438px; height: 335px; z-index: 3;
    background:
      radial-gradient(circle at 65% 25%, #ffd2dc 0%, #f06a8a 18%, #c0466f 40%, transparent 70%),
      linear-gradient(180deg, #9a3d6a 0%, #3a2a55 55%, #0e1126 100%);
  }

  .services__title {
    position: absolute; left: 0; top: 462px; width: 1200px; text-align: center;
    font-family: "Montserrat", Arial, sans-serif; font-weight: 700;
    font-size: 33px; color: var(--white); letter-spacing: 0.5px;
  }
  .services__subtitle {
    position: absolute; left: 0; top: 517px; width: 1200px; text-align: center;
    font-size: 17px; color: var(--white); letter-spacing: 1.9px;
  }

  .benefit { position: absolute; width: 360px; text-align: center; }
  .benefit__icon { display: block; margin: 0 auto; width: 72px; height: 66px; }
  .benefit__text {
    color: var(--white); font-size: 13.8px; line-height: 21px; letter-spacing: 0.3px;
  }
  .benefit--network { left: 214px; top: 574px; }
  .benefit--travel { left: 622px; top: 574px; }
  .benefit--members { left: 214px; top: 750px; }
  .benefit--concierge { left: 622px; top: 750px; }
  .benefit--network .benefit__text,
  .benefit--travel .benefit__text,
  .benefit--members .benefit__text,
  .benefit--concierge .benefit__text { margin-top: 80px; position: absolute; left: 0; top: 0; width: 360px; }
  .benefit__icon { position: absolute; left: 144px; top: 0; }
  .benefit--members .benefit__text,
  .benefit--concierge .benefit__text { margin-top: 80px; }
</style>
</head>
<body>
  <section class="about">
    <h1 class="about__title">ABOUT VELMOR</h1>
    <p class="about__text about__text--first">VELMOR is a members only lifestyle club founded in order to bring the best services, experiences, and opportunities to our diverse community of members.</p>
    <p class="about__text about__text--second">Our members consist of creatives, athletes, artists, and other professionals.</p>
    <a class="button button--learn" href="#">LEARN MORE</a>
  </section>

  <section class="services" role="img" aria-label="Dimmed photo of a crowd dancing at a night event"></section>

  <div class="about__frame"></div>
  <div class="about__photo" role="img" aria-label="Photo of a crowd with raised hands under pink stage lights and confetti"></div>

  <h2 class="services__title">SERVICES &amp; BENEFITS</h2>
  <p class="services__subtitle">THE ULTIMATE FULL SERVICE LIFESTYLE CLUB</p>

  <div class="benefit benefit--network">
    <svg class="benefit__icon" viewBox="0 0 72 66" fill="none" stroke="#fff" stroke-width="1.8">
      <circle cx="36" cy="11" r="7"/><circle cx="16" cy="26" r="7"/><circle cx="50" cy="40" r="7"/><circle cx="27" cy="52" r="7"/>
      <circle cx="8" cy="5" r="2.5"/><circle cx="64" cy="18" r="2.5"/><circle cx="4" cy="52" r="2.5"/><circle cx="48" cy="60" r="2.5"/><circle cx="34" cy="32" r="2.5"/>
      <path d="M8 8v11M43 11l19 6M22 30l10 2M37 32l7 5M6 52h14M34 54l12 5M36 18v12M31 45l15-3"/>
    </svg>
    <p class="benefit__text">VELMOR was formed to bring the best services, experiences, and exclusive opportunities to our members.</p>
  </div>

  <div class="benefit benefit--travel">
    <svg class="benefit__icon" viewBox="0 0 72 66" fill="none" stroke="#fff" stroke-width="1.8">
      <path d="M4 26l8 6h50c4 0 6 2 6 3s-2 3-6 3H14l-8-4z"/>
      <path d="M30 32L38 2h5l-3 30M30 38l8 26h4l-2-26"/>
      <path d="M14 35h40" stroke-dasharray="2 2"/>
      <path d="M10 8h6M20 8h4M56 10h6M14 62h6M24 58h4M58 52h4"/>
    </svg>
    <p class="benefit__text">With everything from private member events to private jet travel, the perks of being a VELMOR member are unmatched.</p>
  </div>

  <div class="benefit benefit--members">
    <svg class="benefit__icon" viewBox="0 0 72 66" fill="none" stroke="#fff" stroke-width="1.8">
      <circle cx="32" cy="20" r="14"/>
      <path d="M12 64c0-14 8-22 20-22s20 8 20 22z"/>
      <circle cx="50" cy="50" r="5"/><path d="M46 54l-8 10"/>
    </svg>
    <p class="benefit__text">Professional athletes, artists, musicians, corporate professionals: Our members come from diverse backgrounds.</p>
  </div>

  <div class="benefit benefit--concierge">
    <svg class="benefit__icon" viewBox="0 0 72 66" fill="none" stroke="#fff" stroke-width="1.8">
      <path d="M32 2h8l1 7 6 3 6-4 6 6-4 6 3 6 7 1v8l-7 1-3 6 4 6-6 6-6-4-6 3-1 7h-8l-1-7-6-3-6 4-6-6 4-6-3-6-7-1v-8l7-1 3-6-4-6 6-6 6 4 6-3z"/>
      <circle cx="36" cy="33" r="17"/>
      <path d="M26 43l14-14M38 25a5 5 0 1 0 7 7M28 41l-2 2"/>
    </svg>
    <p class="benefit__text">Comprehensive services like 24/7 concierge, accountants, attorneys, private advisers, planners, investment advisors and more.</p>
  </div>

  <a class="button button--apply" href="#">APPLY NOW</a>
</body>
</html>
```